The most modern business card ever !!!

Our company call “Vendalo”. Vendalo is a technology company specialized in cruises solutions. Out main product is a platform to reserve cruises. This is a revolutionary platform that make easier to travel agencies and final users to reserve cruises across dozen companies like tibba, wernu, hpv, dgb, etc..We are a “start up”, with a young team of developers and we want to transmit it.. For it, we want something different, a modern business card that represent cruises and technology.. When someone receive this card, this person should say: wowww this is different… this is modern… this is a cruise related company..
- diferent, modern
- traditions business card

```html
<!DOCTYPE html>
<html lang="en">
<head>
<meta charset="utf-8">
<title>Vendalo — Business Card</title>
<link href="https://fonts.googleapis.com/css2?family=Open+Sans:wght@400;600;700&display=swap" rel="stylesheet">
<style>
  :root {
    --stage: #1b1b1c;
    --card: #222224;
    --card-edge: #2c2c2f;
    --white: #ffffff;
    --silver: #8d8f93;
    --text: #d4d4d6;
    --muted: #b9babd;
    --accent: #29a3e0;
    --rule: #4a4b4f;
  }
  * { margin: 0; padding: 0; box-sizing: border-box; }
  html, body { width: 1200px; height: 900px; overflow: hidden; }
  body {
    background: var(--stage);
    font-family: "Open Sans", Arial, sans-serif;
    position: relative;
  }
  .card {
    position: absolute;
    width: 560px;
    height: 320px;
    background: var(--card);
    border: 1px solid var(--card-edge);
    border-radius: 22px;
    box-shadow: 0 18px 40px rgba(0,0,0,0.55);
  }
  .card--back { left: 110px; top: 100px; }
  .card--front { left: 530px; top: 480px; }

  .wordmark {
    position: absolute;
    font-weight: 600;
    letter-spacing: 1px;
    line-height: 1;
  }
  .card--back .wordmark {
    left: 0; right: 0; top: 112px;
    text-align: center;
    font-size: 60px;
    color: var(--silver);
  }
  .website {
    position: absolute;
    left: 0; right: 0; bottom: 34px;
    text-align: center;
    font-size: 13px;
    color: var(--text);
  }

  .card--front .wordmark {
    right: 40px; top: 52px;
    font-size: 58px;
    color: var(--white);
  }
  .divider {
    position: absolute;
    left: 215px; right: 24px; top: 168px;
    height: 1px;
    background: var(--rule);
  }
  .person {
    position: absolute;
    left: 32px; top: 152px;
  }
  .person__name {
    font-size: 18px;
    font-weight: 700;
    color: var(--accent);
    letter-spacing: 0.5px;
  }
  .person__role {
    font-size: 14px;
    color: var(--muted);
    margin-top: -2px;
  }
  .address {
    position: absolute;
    right: 28px; top: 182px;
    text-align: right;
    font-size: 14px;
    line-height: 1.35;
    color: var(--text);
  }
  .contacts {
    position: absolute;
    left: 32px; top: 226px;
    list-style: none;
    font-size: 15px;
    color: var(--text);
    line-height: 1.45;
  }
  .contacts li { display: flex; align-items: center; gap: 7px; }
  .contacts svg { width: 13px; height: 13px; fill: var(--accent); flex: none; }
</style>
</head>
<body>
  <section class="card card--back" aria-label="Card back">
    <div class="wordmark">Vendalo</div>
    <div class="website">www.vendalonet.com</div>
  </section>

  <section class="card card--front" aria-label="Card front">
    <div class="wordmark">Vendalo</div>
    <div class="divider"></div>
    <div class="person">
      <div class="person__name">MARLON AVERY</div>
      <div class="person__role">Managing Director</div>
    </div>
    <div class="address">12345, Address Goes Here<br>Country Name, 123456</div>
    <ul class="contacts">
      <li>
        <svg viewBox="0 0 16 16" aria-hidden="true"><path d="M1 5c0-2 2-3 7-3s7 1 7 3v1h-3V5H4v1H1zM3 7h10l2 7H1zM8 9a2 2 0 100 4 2 2 0 000-4z"/></svg>
        044-987 654 321
      </li>
      <li>
        <svg viewBox="0 0 16 16" aria-hidden="true"><path d="M4 0h8a1 1 0 011 1v14a1 1 0 01-1 1H4a1 1 0 01-1-1V1a1 1 0 011-1zm1 2v10h6V2zm3 11a1 1 0 100 2 1 1 0 000-2z"/></svg>
        044-987 654 321
      </li>
      <li>
        <svg viewBox="0 0 16 16" aria-hidden="true"><path d="M0 3h16v1L8 9 0 4zm0 3l8 5 8-5v7H0z"/></svg>
        hello@vendalomail.com
      </li>
    </ul>
  </section>
</body>
</html>
```